Heron Loan Partners Business Card

We need a business card design for our mortgage servicing company. In addition to servicing the loans of homeowners, we help homeowners with purchasing their homes and any mortgage refinancing. We would like to see designs that use the colors in the logo attached below (gold-ish yellow and navy blue), and any other design you deem fit! The design should communicate a simpler life with smart mortgages provided by Heron.

```html
<!DOCTYPE html>
<html lang="en">
<head>
<meta charset="utf-8">
<title>Heron Loan Partners – Business Card</title>
<link rel="stylesheet" href="https://fonts.googleapis.com/css2?family=Libre+Baskerville:wght@700&family=Poppins:wght@400;500;600&display=swap">
<style>
  :root {
    --navy: #27215a;
    --gold: #e0b13e;
    --white: #ffffff;
    --backdrop: #1d1d1d;
  }
  * { box-sizing: border-box; margin: 0; padding: 0; }
  html, body {
    width: 1200px; height: 1015px; overflow: hidden;
    background: var(--backdrop);
    font-family: "Poppins", sans-serif;
  }
  .sheet { position: relative; width: 1200px; height: 1015px; }
  .card {
    position: absolute; left: 220px; width: 760px; height: 420px;
    overflow: hidden; box-shadow: 0 12px 30px rgba(0,0,0,.55);
  }
  .card--front { top: 70px; background: var(--navy); }
  .card--back { top: 525px; background: var(--white); }
  .card__shape { position: absolute; inset: 0; width: 100%; height: 100%; }
  .brand-name {
    position: absolute; z-index: 1; left: 70px; white-space: nowrap;
    font-family: "Libre Baskerville", serif; font-weight: 700;
    color: var(--gold); font-size: 38px; line-height: 1.2; letter-spacing: .5px;
  }
  .card--front .brand-name { top: 110px; }
  .card--back .brand-name { top: 55px; color: var(--navy); }
  .person {
    position: absolute; z-index: 1; left: 200px; top: 250px; text-align: right; width: 250px;
  }
  .person__name {
    font-family: "Libre Baskerville", serif; font-weight: 700;
    color: var(--gold); font-size: 24px; line-height: 1.2;
  }
  .person__role { color: var(--white); font-size: 17px; font-weight: 500; }
  .divider {
    position: absolute; left: 468px; top: 236px; width: 2px; height: 80px;
    background: var(--gold);
  }
  .contacts { position: absolute; z-index: 1; left: 488px; top: 232px; list-style: none; }
  .contacts li {
    display: flex; align-items: center; gap: 10px;
    color: var(--white); font-size: 16px; line-height: 28px;
  }
  .contacts svg { width: 16px; height: 16px; flex: none; }
  .address {
    position: absolute; z-index: 1; left: 0; right: 0; bottom: 34px; text-align: center;
    color: var(--white); font-size: 17px; letter-spacing: .3px;
  }
</style>
</head>
<body>
<main class="sheet">

  <section class="card card--front" aria-label="Card front">
    <svg class="card__shape" viewBox="0 0 760 420" preserveAspectRatio="none" aria-hidden="true">
      <path fill="var(--gold)" d="M0 395 L150 370 C170 340 185 320 210 325 C240 300 255 305 280 300 C300 330 320 325 330 295 C360 280 380 270 410 268 C440 262 460 250 480 240 C520 225 540 215 560 190 C590 170 610 150 640 140 L760 100 L760 420 L0 420 Z"/>
    </svg>
    <p class="brand-name">Heron Loan Partners</p>
  </section>

  <section class="card card--back" aria-label="Card back">
    <svg class="card__shape" viewBox="0 0 760 420" preserveAspectRatio="none" aria-hidden="true">
      <path fill="var(--navy)" stroke="var(--gold)" stroke-width="3" d="M0 330 L110 300 C130 270 150 255 180 255 C215 240 235 240 260 232 C280 255 300 250 310 225 C340 210 365 200 400 196 C430 190 450 180 470 170 C510 152 530 140 550 120 C580 100 600 85 640 75 L760 40 L760 420 L0 420 Z"/>
    </svg>
    <p class="brand-name">Heron Loan Partners</p>

    <div class="person">
      <p class="person__name">Daniel Hartley</p>
      <p class="person__role">Managing Director</p>
    </div>
    <span class="divider" aria-hidden="true"></span>
    <ul class="contacts">
      <li>
        <svg viewBox="0 0 24 24" aria-hidden="true"><path fill="var(--gold)" d="M6.6 10.8a15 15 0 0 0 6.6 6.6l2.2-2.2a1 1 0 0 1 1-.25 11.4 11.4 0 0 0 3.6.57 1 1 0 0 1 1 1V20a1 1 0 0 1-1 1A17 17 0 0 1 3 4a1 1 0 0 1 1-1h3.5a1 1 0 0 1 1 1c0 1.25.2 2.45.57 3.6a1 1 0 0 1-.25 1z"/></svg>
        044-555 018 274
      </li>
      <li>
        <svg viewBox="0 0 24 24" aria-hidden="true"><path fill="var(--gold)" d="M2 5h20v14H2z M3.5 6.5 12 13l8.5-6.5" stroke="var(--navy)" stroke-width="1.5"/></svg>
        info@heronloans.com
      </li>
      <li>
        <svg viewBox="0 0 24 24" aria-hidden="true"><g fill="none" stroke="var(--gold)" stroke-width="2"><circle cx="12" cy="12" r="9"/><path d="M3 12h18M12 3c3 3 3 15 0 18M12 3c-3 3-3 15 0 18"/></g></svg>
        www.heronloanpartners.com
      </li>
    </ul>
    <p class="address">18 Harbour Street, Bayview 40217, Nationland</p>
  </section>

</main>
</body>
</html>
```